Property Developer Business card design

we need a business card design + printing for a new Property developer company based in melbourne.
We are a group of investors investing in a property developer business. We have more projects involved in residential property as opposed to commercial property but we are involved in both market. we also provide consulting services with overseas investors willing to invest in the australian property market.
Updates
I have uploaded the logo. I'm not very convince with the colors of my logo... any suggestion please?.
Thanks guys!
Target Market(s)
property investors or person willing to purchase investment property
Industry/Entity Type
Residential
Contact Information for Business Card
Bramblecourt Holdings Australia Pty Ltd
Look and feel

```html
<!DOCTYPE html>
<html lang="en">
<head>
<meta charset="utf-8">
<title>Bramblecourt Holdings – Business Card</title>
<link rel="stylesheet" href="https://fonts.googleapis.com/css2?family=Arimo:wght@400;700&display=swap">
<style>
  :root {
    --stage: #e9e6e0;
    --card-top: #2a2a2c;
    --card-bottom: #111112;
    --brand-blue: #2f8fd8;
    --brand-blue-deep: #1d6fc0;
    --brand-red: #c4202c;
    --text-light: #ffffff;
  }
  html, body {
    margin: 0;
    padding: 0;
    width: 1200px;
    height: 800px;
    overflow: hidden;
    background: var(--stage);
    font-family: "Arimo", Arial, sans-serif;
  }
  .stage {
    position: relative;
    width: 1200px;
    height: 800px;
    display: flex;
    justify-content: center;
    align-items: center;
    gap: 40px;
  }
  .card {
    position: relative;
    width: 340px;
    height: 560px;
    border-radius: 22px;
    overflow: hidden;
    background: linear-gradient(160deg, var(--card-top), var(--card-bottom));
    box-shadow: 0 10px 30px rgba(0,0,0,0.25);
  }
  .brand {
    position: absolute;
    left: 0;
    right: 0;
    top: 96px;
    display: flex;
    justify-content: center;
    align-items: center;
    gap: 10px;
  }
  .brand-mark {
    width: 16px;
    height: 16px;
    background: var(--brand-red);
  }
  .brand-name {
    color: var(--brand-blue);
    font-weight: 700;
    font-size: 27px;
    line-height: 1.1;
    text-align: left;
  }
  .contact {
    position: absolute;
    left: 30px;
    top: 232px;
    color: var(--text-light);
    font-size: 17px;
    line-height: 1.3;
  }
  .contact p { margin: 0; }
  .person-name {
    color: var(--brand-blue);
    font-size: 30px;
    margin-bottom: 2px !important;
  }
  .person-role { font-size: 19px; margin-bottom: 10px !important; }
  .label { color: var(--brand-blue); font-size: 18px; }
  .phone { color: var(--brand-blue); font-size: 17px; }
  .address { margin-bottom: 10px !important; }
  .email {
    position: absolute;
    left: 30px;
    top: 460px;
    color: var(--brand-red);
    font-size: 17px;
  }
  .band-blue {
    position: absolute;
    left: 0; right: 0;
    top: 494px;
    height: 10px;
    background: var(--brand-blue-deep);
  }
  .band-red {
    position: absolute;
    left: 0; right: 0;
    top: 504px;
    bottom: 0;
    background: var(--brand-red);
  }
  .legal-name {
    position: absolute;
    left: 0; right: 0;
    bottom: 56px;
    text-align: center;
    color: var(--brand-blue);
    font-size: 15px;
  }
  .legal-name .initial { color: var(--brand-red); }
</style>
</head>
<body>
<main class="stage">
  <section class="card card-front">
    <div class="brand">
      <span class="brand-mark"></span>
      <span class="brand-name">Bramblecourt<br>Holdings</span>
    </div>
    <div class="contact">
      <p class="person-name">Daniel Marsh</p>
      <p class="person-role">Managing Director</p>
      <p class="label">Office address:</p>
      <p class="address">18 Wattlebird Lane<br>Tarneit VIC 3029</p>
      <p class="phone">Telephone : +61 3 9012 5586</p>
      <p class="phone">Mobile : 0400 318 742</p>
    </div>
    <p class="email">daniel.marsh@bramblecourt.com.au</p>
    <div class="band-blue"></div>
    <div class="band-red"></div>
  </section>

  <section class="card card-back">
    <div class="brand">
      <span class="brand-mark"></span>
      <span class="brand-name">Bramblecourt<br>Holdings</span>
    </div>
    <p class="legal-name"><span class="initial">B</span>ramblecourt <span class="initial">H</span>oldings <span class="initial">A</span>ustralia <span class="initial">P</span>ty <span class="initial">L</span>td</p>
  </section>
</main>
</body>
</html>
```